Flight school sign for building, banner, and bilboard

This sign is primarily for use on the side of our flight school building to draw attention for current and future flight school students. We offer airplane and helicopter flight training, ground school training and seminars, airplane and helicopter rentals, multi-engine training, and more. I would like a professional but exciting sign that can be used across a multitude of signage options such as banners, banner ads, billboard, and other mediums so that our sign is consistent and recognizable.

Contact Information for Business Card

The business card should match our company sign somewhat but not exactly. We want good and exciting imagery or wording and energizing/exciting colors.

```html
<!DOCTYPE html>
<html lang="en">
<head>
<meta charset="utf-8">
<title>Zenith Aviation – Flight School Billboard</title>
<link href="https://fonts.googleapis.com/css2?family=Fira+Sans+Condensed:wght@500;600;700;800&family=Montserrat:wght@600&display=swap" rel="stylesheet">
<style>
  :root {
    --page: #efefef;
    --navy: #142348;
    --navy-deep: #0f1c3d;
    --red: #e8202a;
    --sky-top: #2a9be8;
    --sky-mid: #8fcdf2;
    --sky-low: #eef6fc;
    --pale-blue: #9fd3f5;
    --white: #ffffff;
    --text-dark: #18254a;
  }
  * { box-sizing: border-box; margin: 0; padding: 0; }
  html, body { width: 862px; height: 1200px; overflow: hidden; background: var(--page); }
  body { position: relative; font-family: "Fira Sans Condensed", sans-serif; }

  .billboard {
    position: absolute; left: 31px; top: 399px;
    width: 800px; height: 402px; overflow: hidden;
    background: linear-gradient(180deg, var(--sky-top) 0%, var(--sky-mid) 38%, var(--sky-low) 62%, var(--white) 100%);
    box-shadow: 0 12px 22px rgba(0,0,0,.28);
  }
  .billboard__art { position: absolute; inset: 0; }

  .brand { position: absolute; left: 60px; top: 112px; width: 300px; text-align: center; }
  .brand__name {
    display: inline-flex; align-items: center; gap: 8px;
    font-weight: 700; font-size: 27px; letter-spacing: 1.5px; color: var(--navy);
  }
  .brand__dot { width: 14px; height: 14px; border-radius: 50%; background: var(--red); }
  .brand__tagline {
    margin-top: 2px; font-family: "Montserrat", sans-serif; font-weight: 600;
    font-size: 6.5px; letter-spacing: 1.2px; color: var(--red); text-transform: uppercase;
  }

  .offer-heading {
    position: absolute; left: 50px; top: 158px; width: 330px;
    display: flex; align-items: center; gap: 10px;
  }
  .offer-heading__rule { flex: 1; height: 1px; background: var(--navy); }
  .offer-heading__text { font-weight: 800; font-size: 26px; color: var(--red); letter-spacing: .3px; }

  .services { position: absolute; left: 22px; top: 208px; width: 400px;
    display: grid; grid-template-columns: 205px 195px; row-gap: 28px; list-style: none; }
  .service { display: flex; align-items: center; gap: 9px; }
  .service__icon { flex: none; width: 26px; height: 26px; border-radius: 50%; background: var(--red);
    display: flex; align-items: center; justify-content: center; }
  .service__text { font-weight: 600; font-size: 15px; line-height: 1.15; color: var(--text-dark); }

  .contact-bar { position: absolute; left: 0; bottom: 0; width: 470px; height: 58px; background: var(--navy-deep); }
  .contact-phone {
    position: absolute; left: 23px; top: 15px; height: 27px; padding: 0 14px 0 5px;
    border-radius: 14px; background: var(--red); display: flex; align-items: center; gap: 6px;
    font-weight: 600; font-size: 15px; color: var(--white);
  }
  .contact-web { position: absolute; left: 190px; top: 15px; height: 27px; display: flex; align-items: center; gap: 7px;
    font-weight: 700; font-size: 17px; color: var(--white); }
  .contact-web__domain { color: var(--red); }
  .icon-ring { width: 19px; height: 19px; border-radius: 50%; border: 1.5px solid var(--white);
    display: flex; align-items: center; justify-content: center; }
</style>
</head>
<body>
<main class="billboard">
  <svg class="billboard__art" viewBox="0 0 800 402" width="800" height="402">
    <defs>
      <linearGradient id="cockpitTone" x1="0" y1="0" x2="1" y2="1">
        <stop offset="0" stop-color="#d9d2c2"/>
        <stop offset=".45" stop-color="#4a4f66"/>
        <stop offset=".8" stop-color="#2b3355"/>
        <stop offset="1" stop-color="#b0282c"/>
      </linearGradient>
      <radialGradient id="insetTone" cx=".4" cy=".35" r=".7">
        <stop offset="0" stop-color="#f3c77a"/>
        <stop offset=".45" stop-color="#6b5a4e"/>
        <stop offset="1" stop-color="#2a2c3a"/>
      </radialGradient>
    </defs>
    <path class="band band--navy" d="M385,0 C470,25 505,70 522,140 L800,140 V0Z" fill="var(--navy)"/>
    <path class="band band--pale" d="M428,0 C492,30 516,80 528,140 L800,140 V0Z" fill="var(--pale-blue)"/>
    <path class="band band--red" d="M440,0 C520,60 545,150 500,250 C470,320 440,360 440,402 L800,402 V0Z" fill="var(--red)"/>
    <path class="band band--white" d="M518,0 C570,70 580,160 530,260 C505,310 480,360 490,402 L800,402 V0Z" fill="var(--white)"/>
    <path class="photo photo--cockpit" role="img" aria-label="Photo: instructor and student pilot with headsets at the controls of a small training aircraft"
          d="M533,0 C585,70 595,160 545,260 C520,310 497,360 507,402 H800 V0Z" fill="url(#cockpitTone)"/>
    <circle class="photo photo--inset" role="img" aria-label="Photo: airliner flight deck instrument panel at sunrise"
            cx="504" cy="195" r="72" fill="url(#insetTone)"/>
    <circle cx="504" cy="195" r="64" fill="none" stroke="var(--white)" stroke-width="1.2"/>
  </svg>

  <header class="brand">
    <div class="brand__name"><span class="brand__dot"></span>ZENITH AVIATION</div>
    <div class="brand__tagline">Train on the ground, earn your wings</div>
  </header>

  <div class="offer-heading">
    <span class="offer-heading__rule"></span>
    <h2 class="offer-heading__text">WE OFFER</h2>
    <span class="offer-heading__rule"></span>
  </div>

  <ul class="services">
    <li class="service">
      <span class="service__icon"><svg width="14" height="14" viewBox="0 0 24 24"><path d="M2 14l8-3 4-8h2l-2 8 6 1 2-2h1l-1 4 1 4h-1l-2-2-6 1 2 8h-2l-4-8-8-3z" fill="none" stroke="#fff" stroke-width="1.6"/></svg></span>
      <span class="service__text">Airplane and helicopter<br>flight training</span>
    </li>
    <li class="service">
      <span class="service__icon"><svg width="14" height="14" viewBox="0 0 24 24"><rect x="4" y="3" width="16" height="10" rx="1" fill="none" stroke="#fff" stroke-width="1.6"/><path d="M3 20h18M7 16v4M12 16v4M17 16v4" stroke="#fff" stroke-width="1.6"/></svg></span>
      <span class="service__text">Ground school training<br>and seminars</span>
    </li>
    <li class="service">
      <span class="service__icon"><svg width="14" height="14" viewBox="0 0 24 24"><path d="M3 5h18M12 5v4M5 12h11a4 4 0 010 8H9a4 4 0 01-4-4zM5 16H1" fill="none" stroke="#fff" stroke-width="1.6"/></svg></span>
      <span class="service__text">Airplane and<br>helicopter rentals</span>
    </li>
    <li class="service">
      <span class="service__icon"><svg width="14" height="14" viewBox="0 0 24 24"><circle cx="12" cy="12" r="9" fill="none" stroke="#fff" stroke-width="1.6"/><circle cx="12" cy="12" r="3" fill="none" stroke="#fff" stroke-width="1.6"/><path d="M12 3v6M12 15v6M3 12h6M15 12h6" stroke="#fff" stroke-width="1.4"/></svg></span>
      <span class="service__text">Multi-engine training,<br>and more.</span>
    </li>
  </ul>

  <footer class="contact-bar">
    <div class="contact-phone">
      <span class="icon-ring"><svg width="10" height="10" viewBox="0 0 24 24"><path d="M6 2l4 4-2 3a12 12 0 007 7l3-2 4 4-3 4C10 22 2 14 2 5z" fill="#fff"/></svg></span>
      (312) 555 0147
    </div>
    <div class="contact-web">
      <span class="icon-ring"><svg width="11" height="11" viewBox="0 0 24 24"><circle cx="12" cy="12" r="10" fill="none" stroke="#e8202a" stroke-width="2"/><path d="M2 12h20M12 2c4 4 4 16 0 20M12 2c-4 4-4 16 0 20" fill="none" stroke="#e8202a" stroke-width="1.6"/></svg></span>
      <span>www.<span class="contact-web__domain">zenithaviation</span>.com</span>
    </div>
  </footer>
</main>
</body>
</html>
```